E learning Platform for privacy

Current website is as below and its more of a shell.
I need someone to take the text and content and design it properly.
https://study.vornaquill.com/

After that, design has to be implemented with elementor and wordpress
https://elementor.com/

```html
<!DOCTYPE html>
<html lang="en">
<head>
<meta charset="utf-8">
<title>Vornaquill Learning Centre</title>
<link href="https://fonts.googleapis.com/css2?family=Raleway:wght@400;500;600;700;800&display=swap" rel="stylesheet">
<style>
:root{
  --orange:#f26a21;
  --orange-light:#f7962a;
  --ink:#2a2a2a;
  --text:#555;
  --muted:#9a9a9a;
  --line:#e6e6e6;
  --dark:#262626;
  --footer:#303030;
  --white:#fff;
}
*{box-sizing:border-box;margin:0;padding:0}
html,body{width:1200px;height:4494px;overflow:hidden}
body{font-family:"Raleway",sans-serif;color:var(--text);background:var(--white);position:relative}
.btn{display:inline-block;background:var(--orange);color:var(--white);font-weight:600;text-transform:uppercase;border-radius:24px;text-align:center}
.section-title{position:absolute;left:0;width:1200px;text-align:center;font-weight:700;font-size:31px;color:var(--ink);letter-spacing:.3px}
.section-title::after{content:"";display:block;width:92px;height:4px;background:var(--orange);margin:14px auto 0}

/* hero */
.hero{position:absolute;left:0;top:0;width:1200px;height:588px;overflow:hidden}
.hero-photo{position:absolute;inset:0;background:linear-gradient(100deg,#3e3a37 0%,#8a7464 35%,#b59a86 55%,#6d5f58 80%,#3f3b39 100%)}
.hero-shade{position:absolute;inset:0;background:linear-gradient(90deg,rgba(0,0,0,.15),rgba(0,0,0,.35))}
.brand{position:absolute;left:112px;top:52px;color:var(--white);font-weight:800;font-size:40px;letter-spacing:2px;line-height:1}
.brand small{display:block;font-size:8.5px;font-weight:600;letter-spacing:6px;margin-top:6px;padding-left:10px}
.topbar{position:absolute;right:112px;top:20px;display:flex;align-items:center;gap:10px;color:var(--white);font-size:12px}
.topbar .ring{width:30px;height:30px;border:1.5px solid rgba(255,255,255,.7);border-radius:50%;display:flex;align-items:center;justify-content:center}
.topbar b{font-size:16px;font-weight:600}
.nav{position:absolute;left:437px;top:80px;display:flex;gap:25px;color:var(--white);font-size:15px;font-weight:500}
.nav .active{color:var(--orange-light)}
.register{position:absolute;left:934px;top:66px;width:154px;height:50px;line-height:50px;font-size:15px;background:linear-gradient(90deg,var(--orange),var(--orange-light))}
.hero h1{position:absolute;left:561px;top:216px;color:var(--white);font-weight:700;font-size:32px;letter-spacing:-.3px}
.hero p{position:absolute;left:563px;top:272px;color:#f2f2f2;font-size:14.5px}
.hero .cta{position:absolute;left:563px;top:314px;width:155px;height:50px;line-height:50px;font-size:15px}
.dots{position:absolute;left:549px;top:512px;display:flex;gap:14px}
.dots span{width:14px;height:14px;border:1.5px solid var(--white)}
.dots .on{background:var(--orange);border-color:var(--orange)}

/* courses */
.course{position:absolute;top:776px;width:314px;height:459px;background:var(--white);box-shadow:0 1px 6px rgba(0,0,0,.14)}
.course .media{position:absolute;left:6px;top:6px;width:302px;height:243px}
.play{position:absolute;left:50%;top:50%;width:56px;height:56px;margin:-28px 0 0 -28px;border-radius:50%;background:var(--orange);border:3px solid rgba(255,255,255,.85)}
.play::after{content:"";position:absolute;left:21px;top:15px;border-left:17px solid var(--white);border-top:10px solid transparent;border-bottom:10px solid transparent}
.course h3{position:absolute;left:20px;top:273px;font-size:14.5px;font-weight:600;color:var(--ink);white-space:nowrap;overflow:hidden;text-overflow:ellipsis;width:280px}
.course .meta{position:absolute;left:20px;top:306px;font-size:13px;line-height:33px;color:var(--ink)}
.course .read{position:absolute;left:20px;top:405px;width:112px;height:38px;line-height:38px;font-size:13.5px}
.course .tools{position:absolute;right:20px;top:416px;display:flex;gap:18px}
.arrow-btn{position:absolute;top:1006px;width:44px;height:44px;border:1px solid var(--line);border-radius:50%;background:var(--white)}

/* stats */
.stats{position:absolute;left:0;top:1339px;width:1200px;height:320px;background:linear-gradient(90deg,#1e1e1e,#2f2b28 55%,#1c1c1c)}
.stat{position:absolute;top:110px;display:flex;gap:16px}
.stat .num{width:106px;height:106px;border-radius:50%;background:#5b5552;border:4px solid #6e6865;display:flex;align-items:center;justify-content:center;color:var(--orange-light);font-size:26px;font-weight:700;flex:none}
.stat .num.hot{background:var(--orange-light);border-color:#fff3e2;color:var(--white)}
.stat h4{color:var(--white);font-size:12.5px;font-weight:700;margin:14px 0 8px}
.stat p{color:#ddd;font-size:10.5px;line-height:21px;width:200px}

/* why */
.why-art{position:absolute;left:9px;top:1849px;width:427px;height:366px;border-radius:40% 30% 40% 30%;background:radial-gradient(circle at 45% 55%,#d9ecf7 0%,#e9f5fb 55%,#ffffff 80%)}
.feature{position:absolute;width:320px;display:flex;gap:18px}
.feature svg{flex:none}
.feature h4{font-size:13px;font-weight:600;color:var(--ink);white-space:nowrap;overflow:hidden;text-overflow:ellipsis;width:262px;margin-bottom:8px}
.feature p{font-size:10.5px;line-height:24px;color:var(--muted);width:250px}

/* blogs */
.blog{position:absolute;top:2386px;width:320px;height:483px;border:1px solid var(--line);background:var(--white)}
.blog .media{position:absolute;left:7px;top:7px;width:304px;height:216px}
.blog h3{position:absolute;left:14px;top:236px;font-size:14.5px;font-weight:600;color:var(--ink);line-height:27px}
.blog .date{position:absolute;left:14px;top:299px;font-size:14px;color:var(--muted);display:flex;gap:14px;align-items:center}
.blog p{position:absolute;left:14px;top:332px;width:290px;font-size:12.5px;line-height:26px;color:var(--muted);text-align:justify}
.blog .read{position:absolute;left:14px;top:421px;width:128px;height:38px;line-height:38px;font-size:14.5px}
.share{position:absolute;right:22px;top:432px;display:flex;gap:9px}
.share span{width:24px;height:24px;border:1px solid #ddd}

/* testimonials */
.testi{position:absolute;left:0;top:2974px;width:1200px;height:519px;background:linear-gradient(90deg,#f59a3a,#f5a23e 50%,#f39336)}
.testi h2{position:absolute;left:0;width:1200px;top:114px;text-align:center;color:var(--white);font-size:31px;font-weight:700}
.testi .quote{position:absolute;left:150px;width:900px;top:160px;text-align:center;color:var(--white);font-size:14.5px;line-height:34px}
.testi .quote b{font-size:26px;vertical-align:-2px;margin:0 4px}
.avatar{position:absolute;left:542px;top:242px;width:116px;height:116px;border-radius:50%;border:3px solid var(--white);background:linear-gradient(135deg,#c9d7e3,#8aa1b3)}
.testi .name{position:absolute;left:0;width:1200px;top:380px;text-align:center;color:var(--white);font-size:15px}
.testi .role{position:absolute;left:0;width:1200px;top:408px;text-align:center;color:#fff4e6;font-size:14.5px}
.chev{position:absolute;top:240px;width:14px;height:14px;border-left:2px solid var(--white);border-bottom:2px solid var(--white)}

/* about */
.about p{position:absolute;left:120px;top:3676px;width:960px;padding:0 40px;text-align:center;font-size:14.5px;line-height:34px;color:var(--text)}
.about .read{position:absolute;left:523px;top:3860px;width:154px;height:52px;line-height:52px;font-size:15px}

/* footer */
.footer{position:absolute;left:0;top:4015px;width:1200px;height:479px;background:var(--footer);color:#ddd}
.footer .brand{left:112px;top:150px;font-size:52px}
.footer .brand small{font-size:10px;letter-spacing:8px}
.badge{position:absolute;left:112px;top:260px;width:76px;height:26px;background:#e9e9e9;border-radius:2px}
.fcol{position:absolute;top:105px;font-size:14.5px}
.fcol h5{color:var(--white);font-size:14.5px;font-weight:600;margin-bottom:26px}
.fcol li{list-style:none;line-height:43px;color:#e0e0e0}
.social{display:flex;gap:23px;margin-top:6px}
.social span{width:33px;height:33px;border:2px solid #ddd;border-radius:50%}
.hr{position:absolute;left:112px;top:322px;width:976px;height:1px;background:#474747}
.bottom{position:absolute;top:392px;font-size:14px;color:#e0e0e0}
.powered{display:flex;align-items:center;gap:16px}
.partner{font-size:17px;font-weight:600;color:#e0e0e0}
.say-hi{position:absolute;left:1004px;top:0;width:196px;height:98px;display:flex;align-items:center}
.say-hi .face{width:92px;height:92px;border-radius:50%;background:linear-gradient(135deg,#d9cbbd,#a58f7e);border:3px solid var(--white);z-index:1}
.say-hi .tag{margin-left:-30px;height:86px;width:134px;background:var(--orange);color:var(--white);font-size:21px;line-height:22px;padding:22px 0 0 60px}
</style>
</head>
<body>

<header class="hero">
  <div class="hero-photo" role="img" aria-label="Photo of a woman with glasses working on a laptop in a brick-walled office"></div>
  <div class="hero-shade"></div>
  <div class="brand">VORNAQUILL<small>LEARNING CENTRE</small></div>
  <div class="topbar">
    <span class="ring"><svg width="14" height="14" viewBox="0 0 24 24" fill="none" stroke="#fff" stroke-width="2"><path d="M5 3h4l2 5-3 2a12 12 0 0 0 6 6l2-3 5 2v4a2 2 0 0 1-2 2A17 17 0 0 1 3 5a2 2 0 0 1 2-2z"/></svg></span>
    <span>CALL US NOW - <b>+1 (800) 555 0199</b></span>
    <span class="ring" style="margin-left:14px"><svg width="14" height="14" viewBox="0 0 24 24" fill="#fff"><circle cx="12" cy="8" r="5"/><path d="M3 22a9 9 0 0 1 18 0z"/></svg></span>
    <span>SIGN UP</span>
  </div>
  <nav class="nav"><span class="active">HOME</span><span>BLOGS</span><span>COURSES</span><span>CONTACT US</span><span>ABOUT US</span></nav>
  <span class="btn register">REGISTER</span>
  <h1>DATA PROTECTION EXCELLENCE</h1>
  <p>Largest online e-learning resource for data protection &amp; privacy</p>
  <span class="btn cta">GET TRAINED</span>
  <div class="dots"><span></span><span></span><span class="on"></span><span></span></div>
</header>

<h2 class="section-title" style="top:682px">FEATURED COURSES</h2>

<div class="arrow-btn" style="left:60px"><svg width="42" height="42" viewBox="0 0 42 42"><path d="M24 14l-7 7 7 7" fill="none" stroke="#aaa" stroke-width="1.6"/></svg></div>
<div class="arrow-btn" style="left:1096px"><svg width="42" height="42" viewBox="0 0 42 42"><path d="M18 14l7 7-7 7" fill="none" stroke="#aaa" stroke-width="1.6"/></svg></div>

<article class="course" style="left:110px">
  <div class="media" role="img" aria-label="Photo of a woman smiling at her laptop" style="background:linear-gradient(135deg,#d8c9b9,#a57d5e 55%,#e8ddd2)"><span class="play"></span></div>
  <h3>HOW TO SCALE SOCIAL IMPACT</h3>
  <div class="meta">Course Type : Instructor-paced<br>Course Duration : 55Weeks<br>Course Instructors : Mr. Example</div>
  <span class="btn read">READ MORE</span>
  <div class="tools"><svg width="16" height="16" viewBox="0 0 16 16" fill="none" stroke="#555" stroke-width="1.3"><path d="M8 2v8M4 7l4 4 4-4M2 13h12"/></svg><svg width="16" height="16" viewBox="0 0 16 16" fill="none" stroke="#555" stroke-width="1.3"><path d="M9 3l5 4-5 4V9c-4 0-6 1-7 4 0-4 2-7 7-7z"/></svg><svg width="4" height="16" viewBox="0 0 4 16" fill="#555"><circle cx="2" cy="3" r="1.5"/><circle cx="2" cy="8" r="1.5"/><circle cx="2" cy="13" r="1.5"/></svg></div>
</article>
<article class="course" style="left:443px">
  <div class="media" role="img" aria-label="Photo of a woman working at a laptop in a dim room" style="background:linear-gradient(135deg,#6b5b52,#9e8d80 50%,#d8d2cc)"><span class="play"></span></div>
  <h3>GLOBAL SOCIAL ENTREPRENEURSHIP</h3>
  <div class="meta">Course Type : Instructor-paced<br>Course Duration : 107 Weeks<br>Course Instructors : Mr. Example</div>
  <span class="btn read">READ MORE</span>
  <div class="tools"><svg width="16" height="16" viewBox="0 0 16 16" fill="none" stroke="#555" stroke-width="1.3"><path d="M8 2v8M4 7l4 4 4-4M2 13h12"/></svg><svg width="16" height="16" viewBox="0 0 16 16" fill="none" stroke="#555" stroke-width="1.3"><path d="M9 3l5 4-5 4V9c-4 0-6 1-7 4 0-4 2-7 7-7z"/></svg><svg width="4" height="16" viewBox="0 0 4 16" fill="#555"><circle cx="2" cy="3" r="1.5"/><circle cx="2" cy="8" r="1.5"/><circle cx="2" cy="13" r="1.5"/></svg></div>
</article>
<article class="course" style="left:774px">
  <div class="media" role="img" aria-label="Photo of a woman studying at a desk with bookshelves and a plant" style="background:linear-gradient(135deg,#7a5a42,#b89574 50%,#5d4a3c)"><span class="play"></span></div>
  <h3>STUDIO DEMONSTRATION COURSE</h3>
  <div class="meta">Course Type : Instructor-paced<br>Course Duration : 81 Weeks<br>Course Instructors : Mr. Example</div>
  <span class="btn read">READ MORE</span>
  <div class="tools"><svg width="16" height="16" viewBox="0 0 16 16" fill="none" stroke="#555" stroke-width="1.3"><path d="M8 2v8M4 7l4 4 4-4M2 13h12"/></svg><svg width="16" height="16" viewBox="0 0 16 16" fill="none" stroke="#555" stroke-width="1.3"><path d="M9 3l5 4-5 4V9c-4 0-6 1-7 4 0-4 2-7 7-7z"/></svg><svg width="4" height="16" viewBox="0 0 4 16" fill="#555"><circle cx="2" cy="3" r="1.5"/><circle cx="2" cy="8" r="1.5"/><circle cx="2" cy="13" r="1.5"/></svg></div>
</article>

<section class="stats" role="img" aria-label="Dark photo backdrop of a person at a laptop">
  <div class="stat" style="left:110px"><div class="num">6,375</div><div><h4>ENROLLED STUDENTS</h4><p>Nemo enim ipsam voluptatem quia sit aspernatur aut odit aut fugit, consequuntur</p></div></div>
  <div class="stat" style="left:440px"><div class="num hot">114</div><div><h4>LESSONS</h4><p>Nemo enim ipsam voluptatem quia sit aspernatur aut odit aut fugit, consequuntur</p></div></div>
  <div class="stat" style="left:770px"><div class="num">169</div><div><h4>VIDEOS</h4><p>Nemo enim ipsam voluptatem quia sit aspernatur aut odit aut fugit, consequuntur</p></div></div>
</section>

<h2 class="section-title" style="top:1754px">WHY THE (VORNAQUILL) LEARNING CENTRE?</h2>
<div class="why-art" role="img" aria-label="Illustration of a student in an armchair learning on a laptop beside a large video screen and a sleeping cat"></div>

<div class="feature" style="left:462px;top:1858px">
  <svg width="62" height="62" viewBox="0 0 62 62" fill="none" stroke="#f26a21" stroke-width="2"><circle cx="31" cy="33" r="25"/><circle cx="31" cy="33" r="19"/><path d="M24 40l4-11 10-4-4 11z"/><path d="M31 4v4"/></svg>
  <div><h4>COMPREHENSIVE ROADMAP</h4><p>Our objective is to provide a comprehensive competency roadmap, instead of one-off courses</p></div>
</div>
<div class="feature" style="left:820px;top:1858px">
  <svg width="62" height="62" viewBox="0 0 62 62" fill="none" stroke="#f26a21" stroke-width="2"><rect x="4" y="16" width="54" height="36" rx="3"/><path d="M22 16v-6h18v6M4 30h54"/><rect x="26" y="26" width="10" height="8"/></svg>
  <div><h4>OPERATIONAL PERSPECTIVE</h4><p>We cover a broad range of data protection topics from both a legal and operational perspective, covering multiple</p></div>
</div>
<div class="feature" style="left:462px;top:1987px">
  <svg width="62" height="62" viewBox="0 0 62 62" fill="none" stroke="#f26a21" stroke-width="2"><path d="M18 6h26v16a13 13 0 0 1-26 0z"/><path d="M18 12H8c0 10 5 14 11 14M44 12h10c0 10-5 14-11 14M31 35v10M20 56h22l-3-11H23z"/></svg>
  <div><h4>ACADEMIC &amp; INTERNATIONAL CERTIFICATION</h4><p>We partner with prominent universities in the region as well as international certification bodies</p></div>
</div>
<div class="feature" style="left:820px;top:1987px">
  <svg width="62" height="62" viewBox="0 0 62 62" fill="none" stroke="#f26a21" stroke-width="2"><rect x="4" y="6" width="54" height="38" rx="3"/><rect x="14" y="14" width="14" height="20"/><rect x="34" y="14" width="14" height="20"/><path d="M24 44l-3 10h20l-3-10M14 54h34"/></svg>
  <div><h4>MODULAR APPROACH &amp; FLEXIBILITY</h4><p>All our courses are modular in nature to cater to the busy professional, meaning that you can</p></div>
</div>
<div class="feature" style="left:462px;top:2121px">
  <svg width="62" height="62" viewBox="0 0 62 62" fill="none" stroke="#f26a21" stroke-width="2"><path d="M2 18l12-4 10 5 8-3 8 4 10-4 10 4v14l-10 2-16 12-8-6-16-8L2 30z"/><path d="M24 19l-6 8 6 3 8-6"/></svg>
  <div><h4>NETWORK WITH OTHER PEERS</h4><p>Participate in our online communities and discussion rooms and your network with other like-minded</p></div>
</div>
<div class="feature" style="left:820px;top:2121px">
  <svg width="62" height="62" viewBox="0 0 62 62" fill="none" stroke="#f26a21" stroke-width="2"><rect x="14" y="4" width="36" height="44"/><path d="M20 14h24M20 22h24M20 30h14"/><rect x="6" y="12" width="10" height="40"/><circle cx="40" cy="44" r="12"/><path d="M35 44l4 4 7-7"/></svg>
  <div><h4>BUSINESS AND JOB OPPORTUNITIES</h4><p>Collaborate with other professionals on potential business opportunities whether it relates</p></div>
</div>

<h2 class="section-title" style="top:2310px">LATEST BLOGS</h2>

<article class="blog" style="left:110px">
  <div class="media" role="img" aria-label="Photo of a smiling woman holding a tablet by a window" style="background:linear-gradient(120deg,#5e6872,#c8cfd6 50%,#8a9198)"></div>
  <h3>NEMO ENIM IPSAM VOLUPTATEM<br>QUIA VOLUPTAS SIT</h3>
  <div class="date"><svg width="18" height="18" viewBox="0 0 18 18" fill="none" stroke="#999" stroke-width="1.4"><rect x="2" y="3" width="14" height="13"/><path d="M2 7h14M6 1v4M12 1v4"/></svg>December 13, 2019</div>
  <p>Nemo enim ipsam voluptatem quia voluptas sit aspernatur aut odit aut fugit, sed quia consequuntur</p>
  <span class="btn read">READ MORE</span>
  <div class="share"><span></span><span></span><span></span></div>
</article>
<article class="blog" style="left:439px">
  <div class="media" role="img" aria-label="Photo of a cheering woman sitting cross-legged with a laptop on the floor" style="background:linear-gradient(180deg,#f1efec,#e5e1dc 70%,#c7b7a4)"></div>
  <h3>NEMO ENIM IPSAM VOLUPTATEM<br>QUIA VOLUPTAS SIT</h3>
  <div class="date"><svg width="18" height="18" viewBox="0 0 18 18" fill="none" stroke="#999" stroke-width="1.4"><rect x="2" y="3" width="14" height="13"/><path d="M2 7h14M6 1v4M12 1v4"/></svg>December 13, 2019</div>
  <p>Nemo enim ipsam voluptatem quia voluptas sit aspernatur aut odit aut fugit, sed quia consequuntur</p>
  <span class="btn read">READ MORE</span>
  <div class="share"><span></span><span></span><span></span></div>
</article>
<article class="blog" style="left:768px">
  <div class="media" role="img" aria-label="Photo of a man reading a book in a bright room" style="background:linear-gradient(120deg,#8d8a84,#d4cdc3 50%,#6f6a63)"></div>
  <h3>NEMO ENIM IPSAM VOLUPTATEM<br>QUIA VOLUPTAS SIT</h3>
  <div class="date"><svg width="18" height="18" viewBox="0 0 18 18" fill="none" stroke="#999" stroke-width="1.4"><rect x="2" y="3" width="14" height="13"/><path d="M2 7h14M6 1v4M12 1v4"/></svg>December 13, 2019</div>
  <p>Nemo enim ipsam voluptatem quia voluptas sit aspernatur aut odit aut fugit, sed quia consequuntur</p>
  <span class="btn read">READ MORE</span>
  <div class="share"><span></span><span></span><span></span></div>
</article>

<section class="testi">
  <h2>CLIENT TESTIMONIALS</h2>
  <p class="quote"><b>&ldquo;</b>Nemo enim ipsam voluptatem quia voluptas sit aspernatur aut odit aut fugit, sed quia consequuntur magni dolores eos qui ratione voluptatem sequi nesciunt. Neque porro quisquam est,<b>&rdquo;</b></p>
  <div class="avatar" role="img" aria-label="Portrait of the client"></div>
  <div class="name">JHON DOE</div>
  <div class="role">Nemo enim ipsam voluptatem</div>
  <span class="chev" style="left:72px;transform:rotate(45deg)"></span>
  <span class="chev" style="left:1108px;transform:rotate(-135deg)"></span>
</section>

<section class="about">
  <h2 class="section-title" style="top:3585px">ABOUT US</h2>
  <p>Nemo enim ipsam voluptatem quia voluptas sit aspernatur aut odit aut fugit, sed quia consequuntur magni dolores eos qui ratione voluptatem sequi nesciunt. Neque porro quisquam est, qui dolorem ipsum quia dolor sit amet, consectetur, adipisci velit, sed quia non numquam eius modi tempora incidunt ut labore et dolore magnam aliquam quaerat voluptatem. Ut enim ad minima veniam, quis nostrum exercitationem ullam corporis suscipit laboriosam, nisi ut aliquid ex ea commodi consequatur? Quis autem vel eum iure reprehenderit qui in ea voluptate</p>
  <span class="btn read">READ MORE</span>
</section>

<footer class="footer">
  <div class="say-hi"><div class="face" role="img" aria-label="Support agent portrait"></div><div class="tag">say<br>hi</div></div>
  <div class="brand">VORNAQUILL<small>LEARNING CENTRE</small></div>
  <div class="badge" role="img" aria-label="Accessibility conformance badge"></div>
  <div class="fcol" style="left:466px"><h5>COMPANY</h5><ul><li>About</li><li>Courses</li><li>FAQs</li></ul></div>
  <div class="fcol" style="left:673px"><h5>GET INVOLVED</h5><ul><li>Blog</li><li>Contact</li></ul></div>
  <div class="fcol" style="left:882px"><h5>CONNECT</h5><div class="social"><span></span><span></span><span></span><span></span></div></div>
  <div class="hr"></div>
  <div class="bottom" style="left:112px">© 2020 All Rights Reserved</div>
  <div class="bottom powered" style="left:420px;top:388px">Powered by <span class="partner">Pellicrest</span><span class="partner">Havelmoor</span></div>
  <div class="bottom" style="left:778px">Terms of Service Honor Code Privacy Policy</div>
</footer>

</body>
</html>
```